Help design website for "Brightwater Civic Advisors" to advance the common good

Here is the Google doc link that lays out the design:

https://files.plumrivet.example/sheet/d/7QmTzR2wLx9KpVbN4hJcY8sEaUoFdG3iXkMnPq5rWt6/edit?usp=sharing

Here is the Google drive folder with the logos and photos: https://vault.plumrivet.example/open?id=4HkWp9LzQe2TxRvN8mBaYc3DsUoJfG6

The testimonials are being gathered and will be shared by Friday, 1/4.

The winner will also have to migrate the coding files to my hosting site.

Thank you for your help! Looking forward to seeing your designs.

Target Market(s)

Prospective clients

Industry/Entity Type

Non Profit

Coding

Coded - Design and coding required

Number of Pages Required

5+ page

Requirements
Must have
• Noted in the Google doc regarding layout.
Nice to have

```html
<!DOCTYPE html>
<html lang="en">
<head>
<meta charset="utf-8">
<title>Brightwater Civic Advisors</title>
<link href="https://fonts.googleapis.com/css2?family=Raleway:wght@500;600&family=Roboto:ital,wght@0,400;0,500;0,700;1,400&display=swap" rel="stylesheet">
<style>
:root{
  --blue:#0d4c9e;
  --blue-dark:#083a7c;
  --blue-soft:#7f9fcb;
  --page:#f3f3f3;
  --text:#555;
  --muted:#777;
  --white:#fff;
  --line:#b9c6da;
}
*{margin:0;padding:0;box-sizing:border-box}
html,body{width:1200px;height:4196px;overflow:hidden}
body{position:relative;background:var(--page);font-family:"Roboto",Arial,sans-serif;color:var(--text)}
.abs{position:absolute}
/* hero */
.hero{position:absolute;left:0;top:0;width:1200px;height:680px;
  background:linear-gradient(100deg,#2b2e33 0%,#4a4d52 38%,#6b6a68 60%,#3a3c40 100%);
  clip-path:polygon(0 0,100% 0,100% 560px,50% 640px,0 560px)}
.hero::after{content:"";position:absolute;inset:0;background:rgba(0,0,0,.25)}
.hero-chevron{position:absolute;left:0;top:540px}
.nav{position:absolute;top:66px;left:90px;display:flex;gap:34px;z-index:2}
.nav a{color:var(--white);text-decoration:none;font-weight:500;font-size:15px;letter-spacing:.3px}
.brand{position:absolute;top:44px;right:90px;display:flex;align-items:center;gap:12px;z-index:2}
.brand-mark{width:40px;height:40px;border:3px solid var(--white)}
.brand-name{color:var(--white);font-family:"Raleway",sans-serif;font-weight:500;font-size:16px;letter-spacing:4px;line-height:19px;text-transform:uppercase}
.hero-text{position:absolute;left:90px;top:240px;z-index:2;color:var(--white);font-family:"Raleway",sans-serif;font-weight:500;text-transform:uppercase}
.hero-text .small{font-size:34px}
.hero-text h1{font-weight:500;font-size:44px;line-height:52px;margin-top:6px}
.btn-outline{display:inline-block;border:2px solid var(--white);color:var(--white);border-radius:6px;font-family:"Roboto",sans-serif;font-size:15px;text-transform:none;padding:6px 16px;margin-top:26px}
/* headings */
.section-title{position:absolute;left:0;width:1200px;text-align:center;color:var(--blue);font-weight:700;font-size:26px;text-transform:uppercase}
.section-sub{position:absolute;left:0;width:1200px;text-align:center;color:var(--muted);font-size:16px}
/* about */
.about{position:absolute;left:90px;top:760px;width:500px}
.about h2{color:var(--blue);font-size:26px;font-weight:700}
.about p{margin-top:16px;font-size:15.5px;line-height:36px;color:var(--text)}
.btn-blue{display:inline-block;border:2px solid var(--blue);color:var(--blue);border-radius:6px;font-size:15px;font-weight:500;padding:5px 14px;margin-top:26px;background:var(--white)}
.about-photo-frame{position:absolute;left:706px;top:770px;width:364px;height:386px;background:var(--white);box-shadow:0 4px 14px rgba(0,0,0,.25)}
.about-photo{position:absolute;left:690px;top:754px;width:360px;height:386px;background:linear-gradient(160deg,#8f9488,#5a5c55 55%,#2c2d2a);border:6px solid var(--white)}
/* work history */
.client{position:absolute;width:221px;height:142px;background:var(--white);border:3px solid var(--line);box-shadow:0 2px 8px rgba(0,0,0,.15);display:flex;align-items:center;justify-content:center;text-align:center;padding:12px;font-weight:700;font-size:17px;color:#3a4d6c}
/* services */
.service{position:absolute;width:280px;height:180px}
.service::before{content:"";position:absolute;left:20px;top:20px;width:280px;height:180px;background:var(--blue-soft)}
.service .photo{position:absolute;inset:0;background:linear-gradient(135deg,#7a6655,#3b3430)}
.service .cap{position:absolute;left:0;right:0;bottom:0;height:38px;background:var(--blue);color:var(--white);font-weight:700;font-size:12.5px;text-transform:uppercase;display:flex;align-items:center;justify-content:center}
.service.active .photo{background:linear-gradient(135deg,#2f5a93,#1b3f70)}
.service.active .overlay{position:absolute;inset:0;display:flex;flex-direction:column;align-items:center;justify-content:center;color:var(--white);font-weight:700;font-size:15px;text-align:center;line-height:22px;text-transform:uppercase}
.service.active .more{position:absolute;right:22px;bottom:14px;color:var(--white);font-size:13px}
.dots{position:absolute;left:510px;top:2062px}
/* testimonial */
.avatar{position:absolute;left:540px;top:2165px;width:118px;height:118px;border-radius:50%;background:linear-gradient(160deg,#dfe3e8,#9aa3ad);border:5px solid var(--white);box-shadow:0 2px 10px rgba(0,0,0,.2)}
.quote-text{position:absolute;left:270px;top:2372px;width:660px;text-align:center;font-size:16px;line-height:28px;color:var(--text)}
.quote-name{position:absolute;left:0;width:1200px;top:2450px;text-align:center;color:var(--blue);font-weight:700;font-size:15px}
.quote-role{position:absolute;left:0;width:1200px;top:2476px;text-align:center;font-size:12px;color:var(--muted)}
.arrow{position:absolute;top:2378px;color:var(--blue);font-size:22px;font-weight:700}
/* media */
.media{position:absolute;top:2727px;width:293px;height:308px;background:var(--blue)}
.media .photo{position:absolute;left:0;top:0;width:100%;height:210px;background:linear-gradient(150deg,#6d6157,#3e3631)}
.media .icon{position:absolute;left:98px;top:156px;width:96px;height:96px;border-radius:50%;background:var(--blue);border:5px solid var(--white);display:flex;align-items:center;justify-content:center}
.media .label{position:absolute;left:0;right:0;bottom:18px;text-align:center;color:var(--white);font-weight:700;font-size:21px}
/* contact */
.contact-sub{position:absolute;left:0;width:1200px;top:3194px;text-align:center;color:var(--blue);font-weight:700;font-size:20px}
.field{position:absolute;border:3px solid var(--line);border-radius:6px;background:var(--white);color:#9aa;font-style:italic;font-size:15px;padding:10px 14px;box-shadow:0 2px 4px rgba(0,0,0,.08)}
.submit{position:absolute;left:509px;top:3628px;width:165px;height:47px;background:var(--blue);border:3px solid var(--blue-dark);border-radius:6px;color:var(--white);font-weight:700;font-size:19px;display:flex;align-items:center;justify-content:center;box-shadow:0 3px 6px rgba(0,0,0,.25)}
.note{position:absolute;left:0;width:1200px;top:3710px;text-align:center;font-size:15px;font-style:italic;color:#999}
.note b{color:var(--blue)}
/* footer */
.footer{position:absolute;left:0;top:3780px;width:1200px;height:416px}
.footer-brand{position:absolute;left:440px;top:3876px;display:flex;align-items:center;gap:18px}
.footer-brand .brand-mark{width:60px;height:60px}
.footer-brand .brand-name{font-size:24px;letter-spacing:7px;line-height:28px}
.socials{position:absolute;left:0;width:1200px;top:4005px;display:flex;justify-content:center;gap:18px}
.socials span{width:28px;height:28px;border-radius:50%;background:var(--white);opacity:.9}
.info{position:absolute;left:0;width:1200px;text-align:center;color:var(--white);font-size:15px;display:flex;justify-content:center;align-items:center;gap:10px}
.info svg{flex:none}
.copyright{position:absolute;left:0;width:1200px;top:4160px;text-align:center;color:var(--white);font-size:12px}
</style>
</head>
<body>

<!-- Hero -->
<div class="hero" role="img" aria-label="Photo of a smiling professional woman pointing forward with colleagues behind her"></div>
<svg class="hero-chevron" width="1200" height="140" viewBox="0 0 1200 140">
  <polyline points="380,60 600,118 820,60" fill="none" stroke="#0d4c9e" stroke-width="7"/>
  <polyline points="0,20 600,100 1200,20" fill="none" stroke="#ffffff" stroke-width="3" opacity=".6"/>
</svg>
<nav class="nav">
  <a>HOME</a><a>ABOUT</a><a>SERVICES</a><a>TESTIMONIALS</a><a>MEDIA&amp;IMPACT</a><a>CONTACT</a>
</nav>
<div class="brand"><span class="brand-mark"></span><span class="brand-name">Brightwater<br>Civic<br>Advisors</span></div>
<div class="hero-text">
  <div class="small">Welcome to</div>
  <h1>Brightwater<br>Civic Advisors</h1>
  <span class="btn-outline">Read more</span>
</div>

<!-- About -->
<section class="about">
  <h2>ABOUT US</h2>
  <p>Brightwater Civic Advisors supports nonprofit organizations and educational institutions to carry out their missions to benefit the wider community. Founder Dana Whitfield is an educator with a 22-year record of demonstrated achievement and leadership roles in nonprofits and educational institutions. Most recently, she served as Associate Dean of Students in the University and Director of the Campus Service Center at Lakeshore University.</p>
  <span class="btn-blue">Read more</span>
</section>
<div class="about-photo-frame"></div>
<div class="about-photo" role="img" aria-label="Portrait of the founder wearing glasses"></div>

<!-- Work history -->
<h2 class="section-title" style="top:1206px">Work History</h2>
<div class="client" style="left:232px;top:1287px">Campus Service Center</div>
<div class="client" style="left:489px;top:1287px">Coastline Fellows</div>
<div class="client" style="left:747px;top:1287px">Northgate Academy</div>
<div class="client" style="left:232px;top:1479px">Civic Scholars</div>
<div class="client" style="left:489px;top:1479px">Service Corps</div>
<div class="client" style="left:747px;top:1479px">Junction Trust</div>

<!-- Services -->
<h2 class="section-title" style="top:1692px">Services &amp; Testimonials</h2>
<p class="section-sub" style="top:1746px">Dana offers consulting services in six areas to support nonprofits and educational institutions.</p>
<div class="service" style="left:115px;top:1810px">
  <div class="photo" role="img" aria-label="Photo of smiling staff members at a training"></div>
  <div class="cap">Staff Professional Development</div>
</div>
<div class="service active" style="left:456px;top:1810px">
  <div class="photo" role="img" aria-label="Photo of a group facilitation session"></div>
  <div class="overlay">Group Facilitation &amp;<br>Leadership Training</div>
  <div class="more">Read more ›</div>
</div>
<div class="service" style="left:794px;top:1810px">
  <div class="photo" role="img" aria-label="Photo of a speaker at an event podium"></div>
  <div class="cap">Event Planning</div>
</div>
<svg class="dots" width="180" height="16" viewBox="0 0 180 16">
  <line x1="2" y1="8" x2="178" y2="8" stroke="#9bb" stroke-width="1.5"/>
  <circle cx="5" cy="8" r="5" fill="#0d4c9e"/>
  <circle cx="48" cy="8" r="5" fill="#f3f3f3" stroke="#889" stroke-width="1.5"/>
  <circle cx="91" cy="8" r="5" fill="#f3f3f3" stroke="#889" stroke-width="1.5"/>
  <circle cx="134" cy="8" r="5" fill="#f3f3f3" stroke="#889" stroke-width="1.5"/>
  <circle cx="175" cy="8" r="5" fill="#f3f3f3" stroke="#889" stroke-width="1.5"/>
</svg>

<!-- Testimonial -->
<div class="avatar" role="img" aria-label="Portrait of the testimonial author"></div>
<svg class="abs" style="left:572px;top:2314px" width="56" height="32" viewBox="0 0 56 32">
  <path d="M4 30 C0 22 2 8 14 2 C12 10 24 14 20 24 C18 30 8 32 4 30Z" fill="#888"/>
  <path d="M32 30 C28 22 30 8 42 2 C40 10 52 14 48 24 C46 30 36 32 32 30Z" fill="#888"/>
</svg>
<div class="arrow" style="left:108px">&lt;</div>
<div class="arrow" style="left:1082px">&gt;</div>
<p class="quote-text">“ Lorem Ipsum is simply dummy text of the printing and typesetting industry. Lorem Ipsum has been the industry's standard dummy text ever since the 1500s ”</p>
<div class="quote-name">Marcus Delane</div>
<div class="quote-role">Chief Executive Officer, Fair Path Network</div>

<!-- Media -->
<h2 class="section-title" style="top:2598px">Media &amp; Impact</h2>
<p class="section-sub" style="top:2650px">Here is the media coverage for the programs and events that Dana oversaw.</p>
<div class="media" style="left:90px">
  <div class="photo" role="img" aria-label="Photo of a workshop with people seated at round tables"></div>
  <div class="icon"><svg width="44" height="44" viewBox="0 0 44 44" fill="none" stroke="#fff" stroke-width="3"><rect x="6" y="4" width="32" height="36" rx="2"/><line x1="12" y1="12" x2="32" y2="12"/><rect x="12" y="18" width="9" height="9"/><line x1="25" y1="19" x2="32" y2="19"/><line x1="25" y1="26" x2="32" y2="26"/><line x1="12" y1="33" x2="32" y2="33"/></svg></div>
  <div class="label">ARTICLES</div>
</div>
<div class="media" style="left:452px">
  <div class="photo" role="img" aria-label="Photo of a group gathered outdoors"></div>
  <div class="icon"><svg width="44" height="44" viewBox="0 0 44 44" fill="none" stroke="#fff" stroke-width="3"><rect x="4" y="8" width="36" height="28" rx="2"/><line x1="10" y1="8" x2="10" y2="36"/><line x1="34" y1="8" x2="34" y2="36"/><path d="M18 16 L28 22 L18 28Z" fill="#fff"/></svg></div>
  <div class="label">VIDEOS</div>
</div>
<div class="media" style="left:812px">
  <div class="photo" role="img" aria-label="Photo of a speaker at a microphone on a dark stage"></div>
  <div class="icon"><svg width="44" height="44" viewBox="0 0 44 44" fill="none" stroke="#fff" stroke-width="3"><rect x="16" y="4" width="12" height="22" rx="6"/><path d="M10 20 C10 36 34 36 34 20"/><line x1="22" y1="32" x2="22" y2="40"/><line x1="15" y1="40" x2="29" y2="40"/></svg></div>
  <div class="label">PODCAST</div>
</div>

<!-- Contact -->
<h2 class="section-title" style="top:3130px">Contact</h2>
<div class="contact-sub">Book a complimentary consultation</div>
<div class="field" style="left:352px;top:3261px;width:216px;height:46px">First Name</div>
<div class="field" style="left:612px;top:3261px;width:216px;height:46px">Last Name</div>
<div class="field" style="left:352px;top:3339px;width:476px;height:46px">Email Address</div>
<div class="field" style="left:352px;top:3418px;width:476px;height:46px">Subject</div>
<div class="field" style="left:352px;top:3499px;width:476px;height:92px">Message</div>
<div class="submit">SUBMIT</div>
<p class="note"><b>Note</b>: The submissions should be directed to dana@brightwatercivic.example</p>

<!-- Footer -->
<svg class="footer" width="1200" height="416" viewBox="0 0 1200 416">
  <polyline points="180,82 600,18 1020,82" fill="none" stroke="#0d4c9e" stroke-width="6"/>
  <polygon points="0,120 600,34 1200,120 1200,416 0,416" fill="#0d4c9e"/>
</svg>
<div class="footer-brand"><span class="brand-mark"></span><span class="brand-name">Brightwater<br>Civic<br>Advisors</span></div>
<div class="socials"><span></span><span></span><span></span></div>
<div class="info" style="top:4060px">
  <svg width="14" height="14" viewBox="0 0 14 14"><path d="M13 1 L1 6 L6 8 L8 13Z" fill="#fff"/></svg>
  <span>418 Alder Lane, Marlow Springs, OH 40012</span>
  <span style="width:16px"></span>
  <svg width="14" height="14" viewBox="0 0 14 14"><path d="M3 1 L5 1 L6 4 L4.5 5.5 C5.5 7.5 6.5 8.5 8.5 9.5 L10 8 L13 9 L13 11 C13 12 12 13 11 13 C5 13 1 9 1 3 C1 2 2 1 3 1Z" fill="#fff"/></svg>
  <span>555-010-0199</span>
</div>
<div class="info" style="top:4102px">
  <svg width="16" height="12" viewBox="0 0 16 12"><rect x="0" y="0" width="16" height="12" rx="1" fill="#fff"/><polyline points="1,1 8,7 15,1" fill="none" stroke="#0d4c9e" stroke-width="1.5"/></svg>
  <span>info@brightwatercivic.example</span>
  <span style="width:16px"></span>
  <svg width="15" height="15" viewBox="0 0 16 16" fill="none" stroke="#fff" stroke-width="1.5"><circle cx="8" cy="8" r="7"/><ellipse cx="8" cy="8" rx="3" ry="7"/><line x1="1" y1="8" x2="15" y2="8"/></svg>
  <span>www.brightwatercivic.example</span>
</div>
<div class="copyright">Copyrights 2019. All rights reserved</div>

</body>
</html>
```